Website Design for WestaKolory.pl – Luxury Wedding Car Rental with Chauffeur

We are looking for a talented designer to create a modern, elegant, and fully responsive website for our new brand – WestyKolory.pl. We are a premium car rental platform in Poland, offering luxury and exotic vehicles exclusively for weddings. All cars come with a professional chauffeur, ensuring a high-end, stress-free, and stylish experience.
Website Purpose:
The website should present our offering in a luxurious, clear, and inspiring way. It must build trust, highlight the prestige of our brand, and encourage inquiries. Our target audience includes engaged couples, wedding planners, and clients seeking a truly exceptional vehicle for their special day.
Design Requirements:
Style: modern, elegant, minimalist
Color palette: white, black, gold, optionally silver – refined and luxurious
Typography: clean, modern, high-end
Layout: clear, intuitive, with large car images and well-defined sections
Fully responsive (desktop, tablet, mobile)
Bilingual layout (Polish/English) must be considered
Pages to Design:
Homepage
About Us
Fleet Overview
Individual Car Pages
Services (Weddings, Photo Shoots, Film Rentals)
Why Us / Unique Selling Points
Contact
FAQ
Inspiration:
Luxury automotive brands (e.g. Varnel-Hoske, Corvash, Elbrin Tusko)
High-end wedding websites
Minimalist layouts with large visuals and elegant typography
Additional Notes:
The design should evoke the emotions of a wedding day – elegance, uniqueness, style, and class. Please avoid flashy colors, excessive graphic effects, or overly decorative elements. Subtlety, prestige, and sophistication are key.

```html
<!DOCTYPE html>
<html lang="en">
<head>
<meta charset="utf-8">
<title>WestaKolory.pl – Wedding Car Rental</title>
<link href="https://fonts.googleapis.com/css2?family=Jost:wght@400;500;600;700&display=swap" rel="stylesheet">
<style>
:root{
  --gold:#d2b26a;
  --gold-dark:#b8954a;
  --gold-soft:#f3ead6;
  --ink:#1b1b1b;
  --muted:#6e6e6e;
  --line:#e7e2d6;
  --white:#ffffff;
  --maroon:#5a2e2a;
  --star:#e9892e;
}
*{box-sizing:border-box;margin:0;padding:0}
html,body{width:1200px;height:4600px;overflow:hidden;background:var(--white)}
body{font-family:"Jost",sans-serif;color:var(--ink);position:relative}
.abs{position:absolute}
.brand{font-weight:500;color:var(--gold-dark);font-size:22px;display:flex;align-items:center;gap:8px}
.brand .dot{width:14px;height:14px;border-radius:50%;background:var(--gold)}
.nav{top:0;left:0;width:1200px;height:103px}
.nav .brand{position:absolute;left:60px;top:38px}
.nav-links{position:absolute;left:290px;top:40px;display:flex;gap:38px;font-size:15px}
.nav-links a{color:var(--ink);text-decoration:none}
.nav-links a.active{font-weight:600}
.lang{background:var(--gold);color:#fff;border-radius:24px;font-size:15px;font-weight:500;display:flex;align-items:center;gap:10px;padding:0 22px}
.lang .flag{width:22px;height:14px;background:#2b3f83;border-radius:2px}
.photo{background:linear-gradient(135deg,#7b5a3a,#c7a57a 45%,#e9e2d6 60%,#5b4a34)}
.hero-main{left:131px;top:105px;width:938px;height:450px;border-radius:22px}
.hero-side-l{left:0;top:105px;width:112px;height:450px;border-radius:0 22px 22px 0;background:linear-gradient(180deg,#5a3b2c,#a57f6d,#e8e3dd)}
.hero-side-r{left:1089px;top:105px;width:111px;height:450px;border-radius:22px 0 0 22px;background:linear-gradient(180deg,#2e3e22,#4c5f33)}
.hero-card{left:180px;top:182px;width:285px;height:324px;background:#fff;border-radius:18px;padding:20px 20px}
.pill{display:inline-flex;align-items:center;gap:6px;background:var(--maroon);color:#fff;font-size:11px;font-weight:600;border-radius:14px;padding:4px 12px;letter-spacing:.5px}
.hero-card h1{font-size:27px;line-height:35px;font-weight:600;margin-top:12px;width:228px}
.btn-gold{background:var(--gold);color:#fff;font-weight:500;border-radius:30px;display:flex;align-items:center;justify-content:center}
.hero-card .btn-gold{margin-top:14px;height:42px;font-size:14px}
.sec-title{font-size:28px;font-weight:600;text-align:center;width:1200px;left:0}
.feature{width:319px;height:257px;border:1px solid var(--line);border-radius:18px;padding:30px 28px}
.feature .ico{width:38px;height:38px;margin-bottom:26px}
.feature h3{font-size:18px;font-weight:600;margin-bottom:10px}
.feature p{font-size:14px;line-height:26px;color:#333}
.row-title{font-size:30px;font-weight:600}
.btn-outline{border:1.5px solid var(--ink);border-radius:24px;font-size:14px;font-weight:500;display:flex;align-items:center;justify-content:center}
.car-img{width:244px;height:280px;border-radius:18px}
.car-name{font-size:18px;font-weight:600;line-height:28px;width:244px}
.car-price{font-size:14px;color:var(--gold-dark);font-weight:500}
.band{left:0;top:1684px;width:1200px;height:562px;background:linear-gradient(100deg,#fbf6ea 0%,#efe2c2 35%,#d2b26a 80%,#c6a256 100%)}
.band h2{position:absolute;left:52px;top:58px;font-size:38px;font-weight:500}
.see-all{left:821px;top:1738px;width:160px;height:54px;border:1.5px solid #fff;border-radius:28px;color:#fff;font-size:17px;font-weight:600;display:flex;align-items:center;justify-content:center;gap:10px}
.arrow-btn{width:44px;height:44px;border-radius:50%;display:flex;align-items:center;justify-content:center}
.price-card{width:348px;height:364px;background:#fff;border-radius:14px;padding:14px 14px}
.price-card .verified{position:absolute;left:14px;top:12px;font-size:11px;color:#8a7a55;background:#fff8;border-radius:10px;padding:2px 8px;z-index:2;display:flex;align-items:center;gap:4px}
.price-card .pimg{height:168px;border-radius:2px}
.price-card h4{font-size:19px;font-weight:600;line-height:28px;margin-top:24px;width:230px}
.price-card .heart{position:absolute;right:20px;top:204px}
.price-card .meta{font-size:12px;color:var(--muted);margin-top:8px;line-height:26px}
.more{position:absolute;right:14px;bottom:10px;font-size:10px;color:var(--gold-dark);border:1px solid var(--gold);border-radius:10px;padding:1px 10px}
.rent-photo{left:236px;top:2443px;width:321px;height:420px;border-radius:0 40px 40px 40px;background:linear-gradient(160deg,#3a2a22,#8c6b55 40%,#e1d6cf 70%,#6a5244)}
.rent-frame{left:236px;top:2480px;width:321px;height:400px;border-radius:0 0 40px 40px;background:#8b2b2b;z-index:-1}
.avatar-big{left:183px;top:2405px;width:132px;height:132px;border-radius:50%;border:6px solid #fff;background:linear-gradient(135deg,#3a2d28,#b89582);box-shadow:0 4px 14px rgba(0,0,0,.15)}
.quote-card{left:349px;top:2750px;width:272px;height:158px;background:#fff;border-radius:14px;box-shadow:0 8px 24px rgba(0,0,0,.1);padding:24px 22px;font-size:13px;line-height:18px}
.quote-card .who{display:flex;justify-content:space-between;margin-top:18px;font-size:12px;color:#9a9a9a}
.stars{color:var(--star);letter-spacing:2px}
.gold-title{color:var(--gold);font-weight:600}
.q-icon{left:699px;top:2601px;width:68px;height:62px;background:var(--gold);border-radius:14px;display:flex;align-items:center;justify-content:center}
.q-text{left:776px;top:2598px;width:320px;font-size:24px;line-height:28.5px;letter-spacing:1.5px;font-weight:400}
.faq{width:403px;border:1px solid var(--line);border-radius:24px;padding:0 22px;font-size:14px;font-weight:500}
.faq .head{height:47px;display:flex;align-items:center;justify-content:space-between}
.chev{width:22px;height:22px;border:1.5px solid var(--gold);border-radius:50%;display:flex;align-items:center;justify-content:center}
.faq p{font-size:13px;font-weight:400;line-height:25px;color:#333}
.t-card{background:#fff;padding:30px 30px}
.t-card.shadow{box-shadow:0 6px 22px rgba(0,0,0,.09)}
.t-card .person{display:flex;align-items:center;gap:18px;margin:16px 0 24px;font-size:15px;font-weight:600}
.t-card .av{width:66px;height:66px;border-radius:50%;background:linear-gradient(135deg,#3b2e2a,#c49c86)}
.t-card p{font-size:14px;line-height:25px}
.footer{left:0;top:4097px;width:1200px;height:459px;background:linear-gradient(180deg,#d2b26a 0%,#e6d3a6 45%,#fbf8f1 100%)}
.foot-col{font-size:14px;line-height:25px}
.foot-col b{font-weight:600;display:block}
.subscribe{left:680px;top:4223px;width:450px;height:44px;background:#fff;border-radius:24px;display:flex;align-items:center;padding-left:20px;font-size:14px;color:#888;gap:12px}
.subscribe .btn-gold{position:absolute;right:0;top:0;height:44px;width:120px;font-size:14px}
.copyright{left:0;top:4556px;width:1200px;height:44px;border-top:1px solid #cfc6b2;background:#fbf8f1;font-size:15px;display:flex;align-items:center;justify-content:space-between;padding:0 28px}
.socials{display:flex;gap:22px;font-size:12px;font-weight:600}
</style>
</head>
<body>

<header class="abs nav">
  <div class="brand"><span class="dot"></span>WestaKolory.pl</div>
  <nav class="nav-links">
    <a class="active">Homepage</a><a>About Us</a><a>Fleet Overview</a><a>Individual Car Pages</a>
  </nav>
  <div class="abs lang" style="left:938px;top:28px;height:45px;width:192px"><span class="flag"></span>English (UK)
    <svg width="12" height="8" viewBox="0 0 12 8"><path d="M1 1l5 5 5-5" stroke="#fff" stroke-width="1.8" fill="none"/></svg></div>
</header>

<section>
  <div class="abs hero-side-l" role="img" aria-label="Wedding flowers decoration at a venue door"></div>
  <div class="abs photo hero-main" role="img" aria-label="Bride and groom standing by a brick manor house"></div>
  <div class="abs hero-side-r" role="img" aria-label="Green garden foliage"></div>
  <div class="abs hero-card">
    <span class="pill">♛ POPULAR</span>
    <h1>Wedding Car and Dream Car Rental Browse unique, iconic wedding cars</h1>
    <div class="btn-gold">View Wedding Fleet</div>
  </div>
</section>

<h2 class="abs sec-title" style="top:620px">Wedding Car Rental</h2>
<div class="abs feature" style="left:84px;top:684px">
  <svg class="ico" viewBox="0 0 38 38"><circle cx="19" cy="19" r="13" fill="var(--gold)"/><circle cx="19" cy="19" r="5" fill="#fff"/></svg>
  <h3>Convenience</h3>
  <p>No counter, no long lines. We deliver the car to you at the airport, home, hotel or pick it up from our Willow Hills location.</p>
</div>
<div class="abs feature" style="left:441px;top:698px;height:230px">
  <svg class="ico" viewBox="0 0 38 38"><rect x="4" y="8" width="28" height="22" rx="4" fill="var(--gold)"/><rect x="4" y="13" width="28" height="4" fill="#fff"/><circle cx="30" cy="28" r="6" fill="#fff" stroke="var(--gold)" stroke-width="2"/><path d="M27 28l2 2 4-4" stroke="var(--gold)" stroke-width="2" fill="none"/></svg>
  <h3>Quality</h3>
  <p>A wide variety of the latest luxury and exotic cars, always extra clean, always in top condition.</p>
</div>
<div class="abs feature" style="left:797px;top:698px;height:230px">
  <svg class="ico" viewBox="0 0 38 38"><rect x="6" y="6" width="12" height="26" rx="2" fill="var(--gold)"/><rect x="20" y="20" width="12" height="4" fill="var(--gold)"/><circle cx="26" cy="30" r="3" fill="var(--gold)"/></svg>
  <h3>Transparency</h3>
  <p>If it's not listed online, you don't pay for it. No hidden fees, transparent &amp; ready to roll.</p>
</div>

<h2 class="abs row-title" style="left:71px;top:1050px">Choose from Our Exclusive Wedding Fleet</h2>
<div class="abs btn-outline" style="left:1012px;top:1052px;width:118px;height:42px">Explore All</div>

<div class="abs car-img" style="left:71px;top:1123px;background:linear-gradient(160deg,#a99683,#d8d8dc 55%,#7c7a76)" role="img" aria-label="White vintage convertible sedan"></div>
<div class="abs car-img" style="left:343px;top:1123px;background:linear-gradient(160deg,#5e6f4f,#d43a3a 50%,#3b3b3b)" role="img" aria-label="Red open-top sports car"></div>
<div class="abs car-img" style="left:615px;top:1123px;background:linear-gradient(160deg,#2b2b2b,#e7e7e7 55%,#9a9a9a)" role="img" aria-label="White sports coupe front view"></div>
<span class="abs pill" style="left:633px;top:1141px">♛ POPULAR</span>
<div class="abs car-img" style="left:887px;top:1123px;background:linear-gradient(160deg,#3a3a3a,#d9d9d9 50%,#8d8d8d)" role="img" aria-label="White luxury convertible front grille"></div>

<div class="abs car-name" style="left:71px;top:1420px">1976 Cardell Elvada</div>
<div class="abs car-name" style="left:343px;top:1420px">Ferrano<br>F8 Strada</div>
<div class="abs car-name" style="left:615px;top:1420px">Porvane 9 Corsa</div>
<div class="abs car-name" style="left:887px;top:1420px">Varnel-Hoske Aurora<br>(White)</div>
<div class="abs car-price" style="left:71px;top:1490px">$83 / day</div>
<div class="abs car-price" style="left:343px;top:1490px">$995 / day</div>
<div class="abs car-price" style="left:615px;top:1490px">$595 / day</div>
<div class="abs car-price" style="left:887px;top:1490px">$995 / day</div>

<section class="abs band"><h2>Prices for renting our wedding cars</h2></section>
<div class="abs see-all">See all <svg width="14" height="10" viewBox="0 0 14 10"><path d="M1 5h11M8 1l4 4-4 4" stroke="#fff" stroke-width="1.6" fill="none"/></svg></div>
<div class="abs arrow-btn" style="left:1010px;top:1742px;background:#c8a65c"><svg width="10" height="14" viewBox="0 0 10 14"><path d="M8 1L2 7l6 6" stroke="#fff" stroke-width="2" fill="none"/></svg></div>
<div class="abs arrow-btn" style="left:1087px;top:1742px;background:#9b7a3a"><svg width="10" height="14" viewBox="0 0 10 14"><path d="M2 1l6 6-6 6" stroke="#fff" stroke-width="2" fill="none"/></svg></div>

<div class="abs price-card" style="left:51px;top:1824px">
  <span class="verified">✓ Verified</span>
  <div class="pimg" style="background:linear-gradient(160deg,#5c6a4a,#7e93a4 50%,#a3473b)" role="img" aria-label="Vintage sedan parked on a street"></div>
  <h4>1991 Cardell Bramore</h4>
  <svg class="heart" width="18" height="16" viewBox="0 0 18 16"><path d="M9 15S1 10 1 5a4 4 0 018-1 4 4 0 018 1c0 5-8 10-8 10z" stroke="#333" stroke-width="1.5" fill="none"/></svg>
  <div class="meta">€ 2.399,- per day<br>€ 2,50 per kilometer (delivery- till pickup location)</div>
  <span class="more">More Information</span>
</div>
<div class="abs price-card" style="left:418px;top:1824px">
  <span class="verified">✓ Verified</span>
  <div class="pimg" style="background:linear-gradient(160deg,#b9b1a3,#d6d7db 50%,#6f6c67)" role="img" aria-label="White vintage convertible"></div>
  <h4>1976 Cardell Elvada</h4>
  <svg class="heart" width="18" height="16" viewBox="0 0 18 16"><path d="M9 15S1 10 1 5a4 4 0 018-1 4 4 0 018 1c0 5-8 10-8 10z" stroke="#333" stroke-width="1.5" fill="none"/></svg>
  <div class="meta">€ 1.999,- per day<br>€ 2,50 per kilometer (delivery- till pickup location)</div>
  <span class="more">More Information</span>
</div>
<div class="abs price-card" style="left:786px;top:1824px">
  <span class="verified">✓ Verified</span>
  <div class="pimg" style="background:linear-gradient(160deg,#1f2838,#3c4a63 50%,#0e0f12)" role="img" aria-label="Black luxury SUV side view"></div>
  <h4>Cardell Escarra XV 2025</h4>
  <svg class="heart" width="18" height="16" viewBox="0 0 18 16"><path d="M9 15S1 10 1 5a4 4 0 018-1 4 4 0 018 1c0 5-8 10-8 10z" stroke="#333" stroke-width="1.5" fill="none"/></svg>
  <div class="meta">€ 1.599,- per day<br>€ 2,50 per kilometer (delivery- till pickup location)</div>
  <span class="more">More Information</span>
</div>

<div class="abs rent-frame"></div>
<div class="abs rent-photo" role="img" aria-label="Smiling wedding couple beside a car door"></div>
<div class="abs avatar-big" role="img" aria-label="Customer portrait"></div>
<div class="abs quote-card">I would recommend them to everyone<br>and I will use them again in the future!
  <div class="who"><span>Clara J.</span><span class="stars">★★★★★</span></div>
</div>
<div class="abs gold-title" style="left:731px;top:2480px;font-size:24px">Rent one of our wedding cars</div>
<div class="abs q-icon"><svg width="30" height="26" viewBox="0 0 30 26"><path d="M5 12l3-8h14l3 8v9H5z" stroke="#fff" stroke-width="2" fill="none"/><circle cx="10" cy="16" r="2" fill="#fff"/><circle cx="20" cy="16" r="2" fill="#fff"/></svg></div>
<div class="abs q-text">Do you have questions for<br>Velvet Road Studio<br>about renting a<br>wedding car or do you<br>want<br>to book a date in<br>advance?</div>
<div class="abs btn-gold" style="left:731px;top:2874px;width:252px;height:49px;font-size:15px">Contact Us</div>

<h2 class="abs sec-title gold-title" style="top:3026px;font-size:27px">Frequently Asked Questions</h2>
<div class="abs" style="left:0;top:3072px;width:1200px;text-align:center;font-size:14px">Most Common Questions</div>

<div class="abs faq" style="left:193px;top:3141px"><div class="head">How do I make a reservation?<span class="chev"><svg width="10" height="6"><path d="M1 1l4 4 4-4" stroke="#c9a75c" stroke-width="1.5" fill="none"/></svg></span></div></div>
<div class="abs faq" style="left:193px;top:3216px"><div class="head">Will I get the same vehicle that I reserved?<span class="chev"><svg width="10" height="6"><path d="M1 1l4 4 4-4" stroke="#c9a75c" stroke-width="1.5" fill="none"/></svg></span></div></div>
<div class="abs faq" style="left:193px;top:3289px"><div class="head">Do you offer hourly rentals?<span class="chev"><svg width="10" height="6"><path d="M1 1l4 4 4-4" stroke="#c9a75c" stroke-width="1.5" fill="none"/></svg></span></div></div>
<div class="abs faq" style="left:643px;top:3141px"><div class="head">What are your requirements?<span class="chev"><svg width="10" height="6"><path d="M1 1l4 4 4-4" stroke="#c9a75c" stroke-width="1.5" fill="none"/></svg></span></div></div>
<div class="abs faq" style="left:643px;top:3216px;height:135px;border-radius:16px"><div class="head">Do you offer delivery service?<span class="chev"><svg width="10" height="6"><path d="M1 5l4-4 4 4" stroke="#c9a75c" stroke-width="1.5" fill="none"/></svg></span></div>
  <p>Yes, we offer complimentary delivery within<br>Please note: pickup service is also available.</p></div>
<div class="abs faq" style="left:643px;top:3377px"><div class="head">What are your requirements?<span class="chev"><svg width="10" height="6"><path d="M1 1l4 4 4-4" stroke="#c9a75c" stroke-width="1.5" fill="none"/></svg></span></div></div>

<h2 class="abs row-title" style="left:51px;top:3544px;font-size:34px">What our customers say about us</h2>
<div class="abs btn-outline" style="left:1031px;top:3544px;width:118px;height:42px">Explore All</div>

<div class="abs t-card" style="left:75px;top:3656px;width:341px;height:338px">
  <div class="stars" style="font-size:20px">★★★★★</div>
  <div class="person"><span class="av" role="img" aria-label="Customer portrait"></span>Clara J.</div>
  <p>"I'm absolutely delighted with the work delivered by the freelancer I found on this platform. They not only provided high-quality work but also completed it on time. Highly recommend this platform to anyone seeking freelance services"</p>
</div>
<div class="abs t-card shadow" style="left:450px;top:3652px;width:296px;height:361px">
  <div class="stars" style="font-size:20px">★★★★★</div>
  <div class="person"><span class="av" role="img" aria-label="Customer portrait"></span>Gina P.</div>
  <p>They were very accommodating and communication was efficient. We used the gorgeous Varnel-Hoske Aurora for our music video with great success. "</p>
</div>
<div class="abs t-card shadow" style="left:759px;top:3652px;width:360px;height:263px">
  <div class="stars" style="font-size:20px">★★★★★</div>
  <div class="person" style="margin:8px 0 14px"><span class="av" role="img" aria-label="Customer portrait"></span>Ravi M.</div>
  <p>" If you are looking for quality cars and a good service you can't go wrong here. The best car rental service in Willow Hills, no doubt. 3rd time renting from here, never disappointed. "</p>
</div>

<footer class="abs footer"></footer>
<div class="abs brand" style="left:28px;top:4218px;color:#fff;font-size:26px"><span class="dot" style="background:#fff"></span>WestaKolory.pl</div>
<div class="abs" style="left:28px;top:4325px;width:270px;font-size:15px;line-height:24px">Complete your wedding day with one of our special wedding cars or drive them all during our VRS Grand Drive supercar tour!</div>
<div class="abs foot-col" style="left:320px;top:4190px;width:130px"><b>Homepage</b>Individual Car Pages<br>Services</div>
<div class="abs foot-col" style="left:462px;top:4190px"><b>Fleet Overview</b>Why Us</div>
<div class="abs foot-col" style="left:586px;top:4190px"><b>About Us</b>Contact<br><b>FAQ</b></div>
<div class="abs foot-col" style="left:680px;top:4190px"><b>Subscribe &amp; Free Rewards</b></div>
<div class="abs subscribe"><svg width="16" height="12" viewBox="0 0 16 12"><rect x="1" y="1" width="14" height="10" rx="2" fill="#c9c9d8"/></svg>Email Address<div class="btn-gold">Subscribe</div></div>
<div class="abs foot-col" style="left:680px;top:4295px"><b style="font-weight:500">Choose Language</b></div>
<div class="abs lang" style="left:686px;top:4336px;height:44px;width:192px"><span class="flag"></span>English (UK)
  <svg width="12" height="8" viewBox="0 0 12 8"><path d="M1 1l5 5 5-5" stroke="#fff" stroke-width="1.8" fill="none"/></svg></div>

<div class="abs copyright"><span>Copyright © 2025 WestaKolory All Rights Reserved</span>
  <div class="socials"><span>Pictora</span><span>Linkora</span><span>Facenet</span><span>Postly</span></div></div>

</body>
</html>
```